Telecommunications/Power civil contractor needs business card design

Were a new telecommunications/power underground civil contractor that is looking for a new business card design. Our company colours are silver or grey and orange. Feel free to use the white background logo or the black background logo.

Target Market(s)

Local contractors, utility companies, private sector mining/energy companies, developers.

Industry/Entity Type

Telecommunications

Contact Information for Business Card

Each card will need the following info:
Persons name:
Title:
E-mail:
Phone number:
Shop Address:
Mailing Address:

Requirements
Must have
• Each card will need the following info:
• Persons name:
• Title:
• E-mail:
• Phone number:
• Shop Address:
• Mailing Address:

```html
<!DOCTYPE html>
<html lang="en">
<head>
<meta charset="utf-8">
<title>Ridgeline Contracting Inc – Business Card</title>
<link rel="stylesheet" href="https://fonts.googleapis.com/css2?family=Arimo:wght@400;700&display=swap">
<style>
  :root {
    --backdrop: #2b2b2d;
    --card-light: #eeece8;
    --band-pale: #c4c4c4;
    --band-mid: #9a9a9c;
    --card-dark: #58585b;
    --text-light: #f1f1f1;
    --text-soft: #d9d9d9;
    --brand-orange: #e2541f;
    --icon-bg: #d6d6d6;
    --icon-fg: #58585b;
  }
  * { margin: 0; padding: 0; box-sizing: border-box; }
  html, body {
    width: 1200px; height: 997px; overflow: hidden;
    background: var(--backdrop);
    font-family: "Arimo", Arial, sans-serif;
  }
  .canvas {
    position: relative; width: 1200px; height: 997px;
    display: flex; align-items: center; justify-content: center;
  }
  .business-card {
    position: relative; width: 840px; height: 480px;
    border-radius: 22px; overflow: hidden;
    background: var(--card-light);
    box-shadow: 0 24px 50px rgba(0,0,0,.45);
  }
  .card-waves { position: absolute; inset: 0; }
  .brand {
    position: absolute; left: 70px; top: 100px;
    display: flex; align-items: center; gap: 18px;
    color: var(--brand-orange); font-weight: 700;
  }
  .brand-dot {
    width: 64px; height: 64px; border-radius: 50%;
    border: 6px solid var(--brand-orange);
  }
  .brand-name { font-size: 30px; line-height: 1.05; letter-spacing: .5px; }
  .brand-name small { display: block; font-size: 17px; letter-spacing: 2px; }
  .person {
    position: absolute; right: 56px; top: 62px; text-align: right;
    color: var(--text-light);
  }
  .person-name { font-size: 24px; font-variant: small-caps; letter-spacing: .5px; }
  .person-title { font-size: 16px; color: var(--text-soft); margin-top: 2px; }
  .contact-list {
    position: absolute; right: 56px; top: 160px; list-style: none;
    color: var(--text-light); font-size: 17px; text-align: right;
  }
  .contact-item {
    display: flex; justify-content: flex-end; align-items: flex-start;
    gap: 12px; margin-bottom: 16px; line-height: 1.35;
  }
  .contact-icon {
    width: 24px; height: 24px; border-radius: 5px;
    background: var(--icon-bg); flex: none;
    display: flex; align-items: center; justify-content: center;
  }
  .contact-icon svg { width: 16px; height: 16px; fill: var(--icon-fg); }
  .icon-spacer { width: 24px; flex: none; }
  .email {
    position: absolute; left: 56px; bottom: 28px;
    color: var(--text-light); font-size: 18px;
  }
</style>
</head>
<body>
<main class="canvas">
  <article class="business-card">
    <svg class="card-waves" viewBox="0 0 840 480" preserveAspectRatio="none" aria-hidden="true">
      <path fill="var(--band-pale)" d="M520,0 L840,0 L840,480 L0,480 L0,330 C220,330 350,280 420,180 C470,100 480,30 520,0 Z"/>
      <path fill="var(--band-mid)" d="M545,0 L840,0 L840,480 L0,480 L0,368 C230,362 370,300 440,195 C490,110 510,30 545,0 Z"/>
      <path fill="var(--card-dark)" d="M575,0 L840,0 L840,480 L0,480 L0,405 C240,395 390,320 462,210 C515,120 535,30 575,0 Z"/>
    </svg>

    <div class="brand">
      <span class="brand-dot"></span>
      <div class="brand-name">RIDGELINE<small>CONTRACTING INC</small></div>
    </div>

    <div class="person">
      <div class="person-name">Marco L Reyes</div>
      <div class="person-title">Managing Partner</div>
    </div>

    <ul class="contact-list">
      <li class="contact-item">
        <span>+1 (555) 204-3187</span>
        <span class="contact-icon"><svg viewBox="0 0 16 16"><path d="M4 2c1 0 2 2 2 3s-1 1-1 2 2 3 3 3 1-1 2-1 3 1 3 2-1 3-3 3C7 14 2 9 2 4c0-1 1-2 2-2z"/></svg></span>
      </li>
      <li class="contact-item">
        <span>Shop no 42, sec 17, Easton</span>
        <span class="contact-icon"><svg viewBox="0 0 16 16"><path d="M8 2 1 8h2v6h4v-4h2v4h4V8h2z"/></svg></span>
      </li>
      <li class="contact-item">
        <span>28 Birch Row, 1st Floor,<br>Fairview, CT 06000</span>
        <span class="contact-icon"><svg viewBox="0 0 16 16"><path d="M8 1a5 5 0 0 0-5 5c0 4 5 9 5 9s5-5 5-9a5 5 0 0 0-5-5zm0 7a2 2 0 1 1 0-4 2 2 0 0 1 0 4z"/></svg></span>
      </li>
    </ul>

    <div class="email">care@ridgelinecontracting.com</div>
  </article>
</main>
</body>
</html>
```